Biz Card Design TVCP

New business card for a new company.
Logo was completed by a designer on ArtHarbor and looking to continue requesting additional services.
Company Name: Tidal Vector Power Consulting
Although this company is starting in Canada, we will be moving towards a global presence within the next 6 months.
Key elements to this business are as follows.
Energy Procurement
Energy Reduction Services
Demand Side Consulting
Energy Efficiency Consulting
Saving Clients Money
Helping Them Go "Green"
Managing Their Energy Requirements
Basically the goal for our company is to find the best procurement solution for our clients and reduce their energy consumption. This reduces their expenses and the amount of greenhouse gas they produce on a daily basis.
I have been in the energy footprint for the last 20 years and know that most companies are looking to "do whatever is necessary to get them to sign on the dotted line". I would prefer to walk away from a client that I can't help than to put them into a situation that they will regret for years to come. This is where the "TIDAL" part of the company name comes from.
The following is a catch phrase that encompasses what we do.
"Reducing your carbon footprint & energy bill at the same time!"
The back of the card needs to have this statement along with some sort of illustration. The back is a playground for creative ideas.
The front of the card needs the following.
Logo.
First & Last Name (Gus Marwick)
Title (Energy Warrior)
Phone Number (555) 314-2718
Fax Number (555) 271-8314
Email Address gus@tidalvectorpowerconsulting.example
Address 47 fenwick rd Toronto Ontario K4T 2P9
I want it to be a card that is remembered when any of my staff give it to a customer. It HAS to stand out.
Target Market(s)
Business Owners, Decision Makers, 30 to 65+
Industry/Entity Type
Business
Look and feel

```html
<!DOCTYPE html>
<html lang="en">
<head>
<meta charset="utf-8">
<title>Tidal Vector Power Consulting – Business Card</title>
<link href="https://fonts.googleapis.com/css2?family=Ubuntu:wght@700&family=Open+Sans:ital,wght@0,400;0,600;0,700;1,400&display=swap" rel="stylesheet">
<style>
  :root {
    --page-bg: #ecebe8;
    --brand-blue: #3b6db4;
    --brand-blue-deep: #2c5796;
    --leaf-green: #2f9a48;
    --leaf-light: #b5d97a;
    --paper: #ffffff;
    --ink-light: #ffffff;
  }
  * { box-sizing: border-box; margin: 0; padding: 0; }
  html, body {
    width: 1200px; height: 900px; overflow: hidden;
    background: var(--page-bg);
    font-family: "Open Sans", Arial, sans-serif;
  }
  .card-set {
    position: absolute; top: 295px; left: 40px;
    display: flex; gap: 40px;
  }
  .card {
    position: relative; width: 540px; height: 310px;
    border-radius: 20px; overflow: hidden;
    box-shadow: 0 10px 24px rgba(0,0,0,.22);
  }
  /* Back */
  .card--back {
    background: radial-gradient(ellipse at 50% 40%, var(--brand-blue) 0%, var(--brand-blue-deep) 100%);
    color: var(--ink-light);
  }
  .back-wordmark {
    position: absolute; top: 112px; left: 0; right: 0;
    display: flex; align-items: center; justify-content: center; gap: 12px;
    font-family: "Ubuntu", Arial, sans-serif; font-weight: 700;
    font-size: 28px; letter-spacing: -.3px; color: var(--ink-light);
  }
  .back-wordmark .mark-dot {
    width: 18px; height: 18px; border-radius: 50%; background: var(--ink-light);
  }
  .tagline {
    position: absolute; bottom: 34px; left: 0; right: 0; text-align: center;
    font-size: 13px; letter-spacing: .2px;
  }
  /* Front */
  .card--front { background: var(--brand-blue); }
  .front-art { position: absolute; inset: 0; }
  .front-wordmark {
    position: absolute; top: 62px; left: 28px;
    font-family: "Ubuntu", Arial, sans-serif; font-weight: 700;
    font-size: 22px; line-height: 27px; color: var(--brand-blue);
  }
  .holder {
    position: absolute; left: 30px; bottom: 28px; color: var(--ink-light);
  }
  .holder-name { font-size: 19px; font-weight: 700; }
  .holder-title { font-size: 12px; font-weight: 600; margin-top: 2px; }
  .contact-list {
    position: absolute; top: 24px; right: 22px; list-style: none;
    color: var(--ink-light); font-size: 10px; text-align: right;
  }
  .contact-list li {
    display: flex; align-items: center; justify-content: flex-end;
    gap: 6px; height: 19px;
  }
  .contact-list svg { width: 10px; height: 10px; fill: var(--ink-light); flex: none; }
</style>
</head>
<body>
<main class="card-set">
  <section class="card card--back" aria-label="Card back">
    <div class="back-wordmark"><span class="mark-dot"></span>Tidal Vector Power Consulting</div>
    <p class="tagline">"Reducing your carbon footprint &amp; energy bill at the same time!"</p>
  </section>

  <section class="card card--front" aria-label="Card front">
    <svg class="front-art" viewBox="0 0 540 310" aria-hidden="true">
      <defs>
        <linearGradient id="swoosh" x1="1" y1="0" x2="0" y2="1">
          <stop offset="0" stop-color="#b5d97a"/>
          <stop offset=".55" stop-color="#2f9a48"/>
          <stop offset="1" stop-color="#b5d97a"/>
        </linearGradient>
      </defs>
      <path d="M0 0H296C288 130 180 212 0 228Z" fill="url(#swoosh)"/>
      <path d="M0 0H280C272 120 170 196 0 212Z" fill="#ffffff"/>
      <path d="M280 0C272 120 170 196 0 212" fill="none" stroke="#2c5796" stroke-width="2"/>
    </svg>
    <div class="front-wordmark">Tidal Vector<br>Power Consulting</div>
    <ul class="contact-list">
      <li>(555) 314-2718
        <svg viewBox="0 0 10 10"><path d="M2 0l2 2-1 1.5c.6 1.4 1.6 2.4 3 3L7.5 5.5l2 2L8 10C4 9.5.5 6 0 2z"/></svg></li>
      <li>(555) 271-8314
        <svg viewBox="0 0 10 10"><path d="M1 3h8v6H1zM3 0h4v3H3z"/></svg></li>
      <li>gus@tidalvectorpowerconsulting.example
        <svg viewBox="0 0 10 10"><path d="M0 2h10v6H0z M0 2l5 3.5L10 2" stroke="#3b6db4" stroke-width=".8"/></svg></li>
      <li>47 fenwick rd Toronto Ontario K4T 2P9
        <svg viewBox="0 0 10 10"><path d="M5 0l5 5H8.5v5h-2.5V7H4v3H1.5V5H0z"/></svg></li>
    </ul>
    <div class="holder">
      <p class="holder-name">Gus Marwick</p>
      <p class="holder-title">Energy Warrior</p>
    </div>
  </section>
</main>
</body>
</html>
```